Corvana Tongue Works, LLC

We need a business card that includes information about our business and conveys a reliable business that provides document translation services and interpreters for a variety of corporate and individual clients. We want to come across as professional, reliable, yet approachable. It should include the following on one side:

ESL / ENL Language Classes, Private Lessons, and Online Tutors
PLEXA Training and Testing
Translating & Interpreting Services
Contact us about Over-the-Phone Interpreting in over 200 languages
24/7/365
www.corvanatongue.example

The other side should include (555) 481-3062

Rhoda Pelling, President
482 Garnet Ave., Ste. 219
Indianapolis, IN 40917

Please add USA as part of the address. Also, please add rmpelling@corvanatongueworks.example as the e-mail address. Thank you.

Target Market(s)

Business professionals, their families, the international community

Industry/Entity Type

Business

Contact Information for Business Card

24/7/365
www.corvanatongue.example

(555) 481-3062

Rhoda Pelling, President
482 Garnet Ave., Ste. 219
Indianapolis, IN 40917
USA

Font styles to use
Sans Serif

Colors

Designer to choose colors to be used in the design.

Requirements
Must have
• See project description
• e-mail address and web address
• Phone number
Nice to have
• a globe
• physical address
Should not have
• Should not have the same color scheme as other agencies in our market in Indiana unless it is blue and black. No purple or yellow.

```html
<!DOCTYPE html>
<html lang="en">
<head>
<meta charset="utf-8">
<title>Corvana Tongue Works — Business Card</title>
<link rel="stylesheet" href="https://fonts.googleapis.com/css2?family=Lato:wght@400;700;900&display=swap">
<style>
  :root {
    --backdrop: #e7e3de;
    --card: #f7f7f6;
    --ink: #111111;
    --grey: #555555;
    --blue: #2191d0;
    --map: #e4e5e6;
  }
  html, body {
    margin: 0;
    width: 1200px;
    height: 960px;
    overflow: hidden;
    background: var(--backdrop);
    font-family: "Lato", sans-serif;
  }
  .canvas { position: relative; width: 1200px; height: 960px; }
  .card {
    position: absolute;
    width: 600px;
    height: 342px;
    border-radius: 20px;
    background: var(--card);
    overflow: hidden;
    box-shadow: 2px 3px 6px rgba(0,0,0,.35);
  }
  .card-front { left: 302px; top: 129px; }
  .card-back { left: 298px; top: 488px; }

  .front-art { position: absolute; inset: 0; }
  .front-wordmark {
    position: absolute; left: 31px; top: 24px; margin: 0;
    font-size: 34px; font-weight: 400; line-height: 40px; color: var(--ink);
  }
  .person-name {
    position: absolute; left: 31px; top: 156px; margin: 0;
    font-size: 21px; font-weight: 700; color: var(--blue);
  }
  .person-title {
    position: absolute; left: 32px; top: 181px; margin: 0;
    font-size: 15px; font-weight: 700; color: var(--ink);
  }
  .address {
    position: absolute; left: 32px; top: 208px; margin: 0;
    font-size: 14.5px; line-height: 19px; color: var(--grey); font-style: normal;
  }
  .contact-list {
    position: absolute; left: 32px; top: 254px; margin: 0; padding: 0; list-style: none;
    font-size: 14.5px; line-height: 19.5px; color: var(--grey);
  }
  .contact-list li { display: flex; align-items: center; gap: 8px; white-space: nowrap; }
  .contact-list .email { font-size: 12px; }
  .contact-list svg { width: 13px; height: 13px; fill: var(--blue); flex: none; }

  .world-map {
    position: absolute; left: 0; top: 20px; width: 600px; height: 322px;
    background: radial-gradient(ellipse at 50% 45%, var(--map) 0%, rgba(228,229,230,.5) 55%, rgba(247,247,246,0) 80%);
  }
  .back-brand {
    position: absolute; left: 187px; top: 40px;
    display: flex; align-items: center; gap: 10px;
  }
  .brand-dot {
    width: 98px; height: 98px; border-radius: 50%; background: var(--blue);
    flex: none;
  }
  .back-wordmark {
    margin: 0; font-size: 25px; font-weight: 400; line-height: 28px; color: var(--ink);
  }
  .back-copy {
    position: absolute; left: 0; right: 0; text-align: center; margin: 0; color: var(--ink);
  }
  .services { top: 153px; font-size: 14px; line-height: 19px; }
  .services .sep { color: var(--blue); }
  .phone-offer { top: 199px; font-size: 15px; font-weight: 700; line-height: 19px; }
  .hours {
    top: 250px; font-size: 19.5px; font-weight: 900;
    display: flex; justify-content: center; align-items: center; gap: 5px;
  }
  .hours svg { width: 17px; height: 17px; }
  .web-address { top: 279px; font-size: 17px; color: var(--blue); }
  .web-address b { font-weight: 900; }
</style>
</head>
<body>
<main class="canvas">

  <section class="card card-front" aria-label="Card front">
    <svg class="front-art" viewBox="0 0 600 342" width="600" height="342" aria-hidden="true">
      <rect width="600" height="342" fill="var(--ink)"/>
      <path d="M0 0 H470 C565 10 600 100 597 171 C600 250 565 335 470 342 H0 Z" fill="var(--card)"/>
      <circle cx="438" cy="171" r="152" fill="var(--blue)"/>
    </svg>

    <h1 class="front-wordmark">Corvana<br>Tongue<br>Works, LLC</h1>
    <p class="person-name">RHODA PELLING</p>
    <p class="person-title">PRESIDENT</p>
    <address class="address">482 Garnet Ave., Ste. 219<br>Indianapolis, IN 40917, USA</address>
    <ul class="contact-list">
      <li>
        <svg viewBox="0 0 24 24"><path d="M6.6 10.8a15 15 0 0 0 6.6 6.6l2.2-2.2a1 1 0 0 1 1-.25 11.4 11.4 0 0 0 3.6.57 1 1 0 0 1 1 1V20a1 1 0 0 1-1 1A17 17 0 0 1 3 4a1 1 0 0 1 1-1h3.5a1 1 0 0 1 1 1c0 1.25.2 2.45.57 3.57a1 1 0 0 1-.25 1z"/></svg>
        (555) 481-3062
      </li>
      <li class="email">
        <svg viewBox="0 0 24 24"><path d="M2 5h20v14H2z M4 7v.5l8 5 8-5V7l-8 5z" fill-rule="evenodd"/></svg>
        rmpelling@corvanatongueworks.example
      </li>
      <li>
        <svg viewBox="0 0 24 24"><circle cx="12" cy="12" r="10"/><path d="M2 12h20M12 2c3 3 3 17 0 20M12 2c-3 3-3 17 0 20" stroke="var(--card)" stroke-width="1.6" fill="none"/></svg>
        www.corvanatongue.example
      </li>
    </ul>
  </section>

  <section class="card card-back" aria-label="Card back">
    <div class="world-map" role="img" aria-label="Faint world map background"></div>

    <div class="back-brand">
      <span class="brand-dot" aria-hidden="true"></span>
      <h2 class="back-wordmark">Corvana<br>Tongue<br>Works, LLC</h2>
    </div>

    <p class="back-copy services">ESL / ENL Language Classes, Private Lessons, &amp; Online Tutors<br>PLEXA Training &amp; Testing <span class="sep">&#9679;</span> Translating &amp; Interpreting Services</p>
    <p class="back-copy phone-offer">Contact us about Over-the-Phone<br>Interpreting in over 200 languages</p>
    <p class="back-copy hours">
      <svg viewBox="0 0 20 20" aria-hidden="true"><circle cx="10" cy="10" r="8.5" fill="none" stroke="var(--ink)" stroke-width="1.6"/><path d="M10 4.5V10L7 13" fill="none" stroke="var(--ink)" stroke-width="1.6"/></svg>
      24/7/365
    </p>
    <p class="back-copy web-address">www.<b>CORVANATONGUE</b>.example</p>
  </section>

</main>
</body>
</html>
```